Business Card Design

We would like to re-design our business cards. Our Company - Qwinrel Turbochargers, rebuilds turbochargers and sells replacement parts. Our website is: http://www.qwinrelturbochargers-example.com
We just had our logo changed. I will attach the file. Looking for fresh new/modern business card. We like the colors red, black, white and silver. Black background looks attractive, but not a requirement. The final design should communicate reasonable/competitive prices, top quality and reliability of our products.
Updates
Project Deadline Extended
Reason: Need to finalize the info on the card. Currently working on changing address and email info. Want to make sure it is the correct one before accepting the final design. Unless, this is something that can be changed at a later time..??
Industry/Entity Type
Business
Contact Information for Business Card
QWINREL TURBOCHARGERS, LLC
20473 Harwick Lane NE
Massillon, OH 44647
Tel: +1-555-214-7390
Fax: +1-555-267-1842
info@QwinrelTurbochargers-example.com
Our current business card had the following highlights:
*We rebuild all Turbocharges for Automotive, Diesel and Industrial
*Precision Balancing and in-house turbocharger needs
*All Turbocharger replacement parts are made in USA / U.K.
Look and feel
Each slider illustrates characteristics of the customer's brand and the style your logo design should communicate.

```html
<!DOCTYPE html>
<html lang="en">
<head>
<meta charset="utf-8">
<title>Qwinrel Turbochargers – Business Card</title>
<link href="https://fonts.googleapis.com/css2?family=Montserrat:wght@400;500;700;800&family=Open+Sans:wght@600;700&display=swap" rel="stylesheet">
<style>
  :root {
    --page: #e2e2e2;
    --card: #0b0b0c;
    --card-edge: #1a1a1c;
    --red: #e0312b;
    --red-dark: #c4201c;
    --white: #ffffff;
    --silver: #c9c9cc;
  }
  * { box-sizing: border-box; margin: 0; padding: 0; }
  html, body { width: 1200px; height: 852px; overflow: hidden; }
  body {
    background: var(--page);
    font-family: "Montserrat", Arial, sans-serif;
    position: relative;
  }
  .card {
    position: absolute;
    top: 276px;
    width: 520px;
    height: 300px;
    border-radius: 22px;
    background: linear-gradient(135deg, var(--card-edge) 0%, var(--card) 55%, #050505 100%);
    box-shadow: 0 10px 26px rgba(0,0,0,.28);
    overflow: hidden;
    color: var(--white);
  }
  .card--front { left: 60px; }
  .card--back { left: 620px; }

  .turbine-texture {
    position: absolute;
    border-radius: 50%;
    background: radial-gradient(circle, rgba(255,255,255,.06) 0%, rgba(255,255,255,.02) 55%, rgba(255,255,255,0) 72%);
  }
  .card--front .turbine-texture { width: 340px; height: 340px; right: -60px; top: -70px; }
  .card--back .turbine-texture { width: 260px; height: 260px; right: -40px; top: 10px; }

  .wordmark {
    position: absolute;
    display: flex;
    align-items: center;
    gap: 12px;
    font-weight: 800;
    color: var(--white);
    letter-spacing: .2px;
    line-height: 1.02;
  }
  .wordmark__dot {
    width: 46px; height: 46px;
    border-radius: 50%;
    background: var(--red);
    flex: none;
  }
  .wordmark__name { font-size: 26px; }
  .wordmark__name span { display: block; font-size: 19px; }

  .card--front .wordmark { left: 110px; top: 108px; }
  .card--back .wordmark { right: 36px; top: 48px; }
  .card--back .wordmark__dot { width: 40px; height: 40px; }
  .card--back .wordmark__name { font-size: 22px; }
  .card--back .wordmark__name span { font-size: 16px; }

  .rule { position: absolute; height: 2px; background: var(--red); }
  .rule--top { right: 0; top: 86px; width: 110px; }
  .rule--bottom { left: 0; bottom: 54px; width: 120px; }

  .front-url {
    position: absolute;
    left: 170px; bottom: 74px;
    font-size: 14px;
    font-weight: 500;
    color: var(--white);
  }

  .name-tag {
    position: absolute;
    left: 0; top: 178px;
    width: 250px; height: 40px;
    background: linear-gradient(90deg, var(--red-dark), var(--red));
    border-radius: 0 10px 10px 0;
    display: flex; align-items: center;
    padding-left: 34px;
    font-family: "Open Sans", Arial, sans-serif;
    font-weight: 700;
    font-size: 17px;
  }

  .address {
    position: absolute;
    left: 300px; top: 128px;
    display: flex; gap: 10px;
    font-size: 12.5px;
    line-height: 1.55;
    color: var(--white);
  }

  .contacts {
    position: absolute;
    left: 34px; top: 232px;
    list-style: none;
    font-size: 12.5px;
    line-height: 20px;
  }
  .contacts li { display: flex; align-items: center; gap: 9px; }
  .contacts svg { width: 12px; height: 12px; fill: var(--red); flex: none; }
  .contacts .accent { color: var(--red); }
</style>
</head>
<body>

<section class="card card--front" aria-label="Card front">
  <div class="turbine-texture" role="img" aria-label="Faint turbine wheel texture"></div>
  <div class="rule rule--top"></div>
  <div class="wordmark">
    <div class="wordmark__dot"></div>
    <div class="wordmark__name">Qwinrel<span>Turbochargers</span></div>
  </div>
  <p class="front-url">www.QwinrelTurbochargers-example.com</p>
  <div class="rule rule--bottom"></div>
</section>

<section class="card card--back" aria-label="Card back">
  <div class="turbine-texture" role="img" aria-label="Faint turbine wheel texture"></div>
  <div class="wordmark">
    <div class="wordmark__dot"></div>
    <div class="wordmark__name">Qwinrel<span>Turbochargers</span></div>
  </div>

  <div class="address">
    <svg width="12" height="16" viewBox="0 0 12 16" aria-hidden="true"><path fill="#e0312b" d="M6 0a6 6 0 0 0-6 6c0 4.5 6 10 6 10s6-5.5 6-10a6 6 0 0 0-6-6zm0 8.3A2.3 2.3 0 1 1 6 3.7a2.3 2.3 0 0 1 0 4.6z"/></svg>
    <p>5182 Denholm Ave. NW<br>North Ferrisdale, Ohio</p>
  </div>

  <div class="name-tag">Your Long Name</div>

  <ul class="contacts">
    <li>
      <svg viewBox="0 0 12 12" aria-hidden="true"><path d="M2.4 0.6 4.3 2.8 3.3 4.3c.7 1.6 2 2.9 3.6 3.6l1.5-1 2.2 1.9-1 2.2C5 11 1 7 .3 1.6z"/></svg>
      1.555.214.7390
    </li>
    <li>
      <svg viewBox="0 0 12 12" aria-hidden="true"><path d="M0 2h12v8H0zM1 3l5 3.5L11 3v-.2H1z" fill-rule="evenodd"/></svg>
      info@QwinrelTurbochargers-example.com
    </li>
    <li>
      <svg viewBox="0 0 12 12" aria-hidden="true"><circle cx="6" cy="6" r="6"/><path d="M0 6h12M6 0c-2.4 3-2.4 9 0 12M6 0c2.4 3 2.4 9 0 12" stroke="#0b0b0c" stroke-width=".9" fill="none"/></svg>
      www.<span class="accent">QwinrelTurbochargers-example</span>.com
    </li>
  </ul>
</section>

</body>
</html>
```